New Zealand Marlborough Sauvignon Blanc wine packaging design

We need packaging design for our new wine brand, Dunmore Vale. The wine is a New Zealand Marlborough Sauvignon Blanc. We would like the packaging will portray elegance and style with an understated label. We are looking for a label that portrays the elegance of the French Riviera. The label should be round or pill shaped.
Updates

Industry/Entity Type

Wine

Font styles to use
Serif
Sans Serif

Requirements
Must have
• The words in order of importance: Dunmore Vale, Sauvignon Blanc, Marlborough, New Zealand. It should be fit to the bottle posted in the links
Nice to have
• a pill shape or circular shape
Should not have
• Illustrations of wine bottles, wine glasses, or grapes

```html
<!DOCTYPE html>
<html lang="en">
<head>
<meta charset="utf-8">
<title>Dunmore Vale Sauvignon Blanc Label</title>
<link rel="stylesheet" href="https://fonts.googleapis.com/css2?family=Playfair+Display:wght@500&family=Allura&display=swap">
<style>
  :root {
    --canvas-bg: #eef2d2;
    --label-bg: #ffffff;
    --ink-olive: #5c6b22;
    --wash-light: #e3e8cf;
    --wash-mid: #cfd8b0;
    --leaf-sage: #a9b58e;
    --petal-white: #f6f7ef;
  }
  * { margin: 0; padding: 0; box-sizing: border-box; }
  html, body {
    width: 1200px;
    height: 675px;
    overflow: hidden;
    background: var(--canvas-bg);
  }
  .canvas {
    position: relative;
    width: 1200px;
    height: 675px;
    background: var(--canvas-bg);
  }
  .label {
    position: absolute;
    left: 421px;
    top: 79px;
    width: 359px;
    height: 522px;
    border-radius: 180px;
    background: var(--label-bg);
    overflow: hidden;
  }
  .wash {
    position: absolute;
    border-radius: 50%;
    filter: blur(8px);
  }
  .wash--top {
    left: 40px; top: -20px; width: 330px; height: 230px;
    background: radial-gradient(ellipse at 55% 45%, var(--wash-mid) 0%, var(--wash-light) 50%, rgba(255,255,255,0) 75%);
  }
  .wash--bottom {
    left: -20px; top: 340px; width: 340px; height: 220px;
    background: radial-gradient(ellipse at 45% 55%, var(--wash-mid) 0%, var(--wash-light) 50%, rgba(255,255,255,0) 78%);
  }
  .floral {
    position: absolute;
    border-radius: 45%;
    filter: blur(6px);
    opacity: 0.6;
  }
  .floral--branch {
    left: 200px; top: 28px; width: 160px; height: 140px;
    background: radial-gradient(ellipse at 55% 55%, var(--petal-white) 0%, var(--leaf-sage) 45%, rgba(169,181,142,0) 72%);
  }
  .floral--daisies {
    left: 22px; top: 300px; width: 90px; height: 190px;
    background: radial-gradient(ellipse at 50% 35%, var(--petal-white) 0%, var(--leaf-sage) 50%, rgba(169,181,142,0) 75%);
  }
  .brand-name {
    position: absolute;
    left: 0; top: 0;
    font-family: "Playfair Display", serif;
    font-weight: 500;
    color: var(--ink-olive);
    font-size: 70px;
    line-height: 1;
    letter-spacing: -1px;
  }
  .brand-name__line {
    position: absolute;
    white-space: nowrap;
  }
  .brand-name__line--first { left: 30px; top: 160px; }
  .brand-name__line--second { left: 128px; top: 222px; }
  .varietal {
    position: absolute;
    left: 100px;
    top: 298px;
    font-family: "Allura", cursive;
    font-size: 36px;
    line-height: 1;
    color: var(--ink-olive);
    white-space: nowrap;
  }
  .region {
    position: absolute;
    left: 0; top: 0;
    width: 359px; height: 522px;
  }
  .region text {
    font-family: "Playfair Display", serif;
    font-weight: 500;
    font-size: 18px;
    fill: var(--ink-olive);
  }
</style>
</head>
<body>
<main class="canvas">
  <section class="label" aria-label="Dunmore Vale Sauvignon Blanc wine label">
    <div class="wash wash--top" role="img" aria-label="Soft sage watercolour wash"></div>
    <div class="wash wash--bottom" role="img" aria-label="Soft sage watercolour wash"></div>
    <div class="floral floral--branch" role="img" aria-label="Watercolour daisy on a leafy branch"></div>
    <div class="floral floral--daisies" role="img" aria-label="Watercolour cluster of white daisies with sage leaves"></div>

    <h1 class="brand-name">
      <span class="brand-name__line brand-name__line--first">Dunmore</span>
      <span class="brand-name__line brand-name__line--second">Vale</span>
    </h1>
    <p class="varietal">Sauvignon Blanc</p>

    <svg class="region" viewBox="0 0 359 522" aria-label="Marlborough, New Zealand">
      <defs>
        <path id="region-arc" d="M 84 466 Q 186 540 286 452" fill="none"/>
      </defs>
      <text>
        <textPath href="#region-arc" startOffset="50%" text-anchor="middle">Marlborough, New Zealand</textPath>
      </text>
    </svg>
  </section>
</main>
</body>
</html>
```